Telecommunications/Power civil contractor needs business card design

Were a new telecommunications/power underground civil contractor that is looking for a new business card design. Our company colours are silver or grey and orange. Feel free to use the white background logo or the black background logo.

Target Market(s)

Local contractors, utility companies, private sector mining/energy companies, developers.

Industry/Entity Type

Telecommunications

Contact Information for Business Card

Each card will need the following info:
Persons name:
Title:
E-mail:
Phone number:
Shop Address:
Mailing Address:

Requirements
Must have
• Each card will need the following info:
• Persons name:
• Title:
• E-mail:
• Phone number:
• Shop Address:
• Mailing Address:

```html
<!DOCTYPE html>
<html lang="en">
<head>
<meta charset="utf-8">
<title>Trenchline Civil Inc – Business Card</title>
<link rel="stylesheet" href="https://fonts.googleapis.com/css2?family=Open+Sans:wght@400;600;700&display=swap">
<style>
  :root {
    --orange: #f05f24;
    --paper: #ececec;
    --silver: #b9b9b9;
    --grey: #6f6f6f;
    --muted: #9a9a9a;
    --white: #ffffff;
    --backdrop: #4b3125;
  }
  * { margin: 0; padding: 0; box-sizing: border-box; }
  html, body { width: 1200px; height: 864px; overflow: hidden; }
  body {
    background: var(--backdrop);
    font-family: "Open Sans", Arial, sans-serif;
    position: relative;
  }
  .card {
    position: absolute;
    left: 320px;
    width: 560px;
    height: 320px;
    overflow: hidden;
    background: var(--orange);
    box-shadow: 0 10px 28px rgba(0,0,0,.45);
  }
  .card-front { top: 92px; }
  .card-back { top: 452px; }

  /* Front */
  .front-brand {
    position: absolute; inset: 0;
    display: flex; flex-direction: column; align-items: center; justify-content: center;
    gap: 18px;
  }
  .brand-dot {
    width: 110px; height: 110px; border-radius: 50%;
    border: 7px solid var(--white);
  }
  .front-brand .brand-name {
    color: var(--white); font-weight: 700; font-size: 32px; letter-spacing: 2px;
    text-transform: uppercase;
  }

  /* Back */
  .back-shape { position: absolute; inset: 0; }
  .contact {
    position: absolute; left: 34px; top: 30px; color: var(--white);
  }
  .person-name { font-size: 27px; font-weight: 400; line-height: 1.1; }
  .person-title { font-size: 15px; color: var(--muted); margin-bottom: 14px; }
  .address { font-size: 14px; line-height: 1.35; margin-bottom: 10px; }
  .lines { list-style: none; font-size: 14px; line-height: 1.4; }
  .lines li { display: flex; align-items: center; gap: 8px; }
  .icon { width: 14px; height: 14px; flex: none; }
  .back-brand {
    position: absolute; right: 34px; bottom: 30px;
    display: flex; align-items: center; gap: 14px;
  }
  .back-brand .brand-name {
    color: var(--orange); font-weight: 700; font-size: 22px; letter-spacing: 1px;
    text-transform: uppercase; line-height: 1.1; text-align: right;
  }
  .back-brand .brand-dot {
    width: 64px; height: 64px; border: 5px solid var(--grey);
  }
</style>
</head>
<body>

<section class="card card-front">
  <div class="front-brand">
    <div class="brand-dot"></div>
    <div class="brand-name">Trenchline Civil Inc</div>
  </div>
</section>

<section class="card card-back">
  <svg class="back-shape" width="560" height="320" viewBox="0 0 560 320">
    <path d="M0 320 L0 280 Q280 230 560 130 L560 320 Z" fill="var(--paper)"/>
    <path d="M0 280 Q280 230 560 130" fill="none" stroke="var(--silver)" stroke-width="5"/>
  </svg>

  <div class="contact">
    <div class="person-name">John Smith</div>
    <div class="person-title">General Manager</div>
    <div class="address">Street Address, Suite 00<br>Statename 00000</div>
    <ul class="lines">
      <li>
        <svg class="icon" viewBox="0 0 14 14"><rect width="14" height="14" rx="3" fill="#fff"/><path d="M4 3.5h2l.6 2-1 .8a5 5 0 0 0 2.1 2.1l.8-1 2 .6v2a1 1 0 0 1-1 1A6.5 6.5 0 0 1 3 4.5a1 1 0 0 1 1-1z" fill="var(--orange)"/></svg>
        555 0142 7788
      </li>
      <li>
        <svg class="icon" viewBox="0 0 14 14"><rect width="14" height="14" rx="3" fill="#fff"/><rect x="4.5" y="2.5" width="5" height="9" rx="1" fill="var(--orange)"/></svg>
        555 0199 3412
      </li>
      <li>
        <svg class="icon" viewBox="0 0 14 14"><rect width="14" height="14" rx="3" fill="#fff"/><rect x="2.5" y="4" width="9" height="6" fill="var(--orange)"/><path d="M2.5 4l4.5 3.5L11.5 4" fill="none" stroke="#fff" stroke-width="1"/></svg>
        info@trenchlinecivil.com
      </li>
      <li>
        <svg class="icon" viewBox="0 0 14 14"><rect width="14" height="14" rx="3" fill="#fff"/><circle cx="7" cy="7" r="4" fill="none" stroke="var(--orange)" stroke-width="1.3"/><path d="M3 7h8M7 3v8" stroke="var(--orange)" stroke-width="1"/></svg>
        www.trenchlinecivil.com
      </li>
    </ul>
  </div>

  <div class="back-brand">
    <div class="brand-name">Trenchline<br>Civil Inc</div>
    <div class="brand-dot"></div>
  </div>
</section>

</body>
</html>
```